Packaging design for a reclosable bag for our product

We have a logo, and we need to put it on packaging for our product and while we want the look to be simple, we want it to follow good design principles and also contain spaces for other product descriptions.

There will be 5 sizes at launch so I'd like 5 variations, one for each size.

I've included a few mockups of the type of bag that I made but they are all just rough ideas that I had.

I want the brand to look scientific and methodical and even a bit quirky, as in "wow this is a serious product but also a bit unusual."

```html
<!DOCTYPE html>
<html lang="en">
<head>
<meta charset="UTF-8">
<title>Bias Lighting Pouch – QV7</title>
<link rel="stylesheet" href="https://fonts.googleapis.com/css2?family=Barlow:wght@500;600;700&family=Barlow+Semi+Condensed:wght@500;600;700&display=swap">
<style>
  :root {
    --backdrop: #2b2c2f;
    --pouch: #0b0b0c;
    --pouch-seam: #1c1c1e;
    --ink-light: #f2f2f2;
    --ink-dark: #0b0b0c;
    --text-font: "Barlow", sans-serif;
    --condensed-font: "Barlow Semi Condensed", sans-serif;
  }
  * { margin: 0; padding: 0; box-sizing: border-box; }
  html, body {
    width: 1200px; height: 833px; overflow: hidden;
    background: var(--backdrop);
  }
  .canvas { position: relative; width: 1200px; height: 833px; }

  .pouch {
    position: absolute; left: 358px; top: 110px;
    width: 484px; height: 692px;
    background: var(--pouch);
    color: var(--ink-light);
    font-family: var(--text-font);
    overflow: hidden;
  }
  .zip-line {
    position: absolute; left: 0; right: 0; top: 72px;
    height: 2px; background: var(--pouch-seam);
  }
  .spec-line {
    position: absolute; top: 26px; left: 0; right: 0;
    display: flex; justify-content: center; align-items: center; gap: 6px;
    font-family: var(--condensed-font); font-weight: 600;
    font-size: 14px; letter-spacing: 0.5px;
  }
  .spec-line svg { width: 15px; height: 15px; }

  .length-badge {
    position: absolute; left: 50px; top: 146px;
    width: 58px; height: 58px; border-radius: 50%;
    background: var(--ink-light); color: var(--ink-dark);
    display: flex; flex-direction: column; align-items: center; justify-content: center;
    font-family: var(--condensed-font); font-weight: 700; line-height: 1;
  }
  .length-badge .value { font-size: 23px; }
  .length-badge .unit { font-size: 8.5px; font-weight: 600; margin-top: 3px; }

  .category {
    position: absolute; top: 232px; left: 0; right: 0;
    text-align: center; font-weight: 600;
    font-size: 27px; letter-spacing: 5px;
  }
  .size-pill {
    position: absolute; left: 105px; top: 264px;
    width: 262px; height: 23px; border-radius: 12px;
    background: var(--ink-light); color: var(--ink-dark);
    display: flex; align-items: center; justify-content: center;
    font-size: 10px; font-weight: 500; letter-spacing: 8px;
  }
  .product-name {
    position: absolute; top: 292px; left: 0; right: 0;
    text-align: center; font-family: var(--text-font); font-weight: 700;
    font-size: 206px; line-height: 1; letter-spacing: -8px;
    color: var(--ink-light);
  }

  .dot-band {
    position: absolute; left: 32px; right: 32px; top: 522px; bottom: 10px;
    background: radial-gradient(ellipse 60% 75% at 50% 60%, #d8d8d8 0%, #8a8a8a 45%, #2a2a2a 85%, #161616 100%);
  }
  .temperature-disc {
    position: absolute; left: 177px; top: 537px;
    width: 124px; height: 124px; border-radius: 50%;
    background: var(--pouch);
    display: flex; flex-direction: column; align-items: center; justify-content: center;
    font-family: var(--condensed-font); line-height: 1;
  }
  .temperature-disc .kelvin { font-size: 35px; font-weight: 700; }
  .temperature-disc .label { font-size: 9.5px; font-weight: 500; margin-top: 4px; letter-spacing: 0.3px; }
</style>
</head>
<body>
<div class="canvas">
  <div class="pouch">
    <div class="spec-line">
      <svg viewBox="0 0 16 16" fill="none" stroke="currentColor" stroke-width="1.3" aria-hidden="true">
        <circle cx="8" cy="8" r="3"/>
        <path d="M8 1v2M8 13v2M1 8h2M13 8h2M3 3l1.4 1.4M11.6 11.6L13 13M3 13l1.4-1.4M11.6 4.4L13 3"/>
      </svg>
      <span>SIMULATED D65 CRI 90+</span>
    </div>
    <div class="zip-line"></div>

    <div class="length-badge">
      <span class="value">5</span>
      <span class="unit">METERS</span>
    </div>

    <div class="category">BIAS LIGHTING</div>
    <div class="size-pill">EXTRA LARGUE</div>

    <div class="product-name">QV7</div>

    <div class="dot-band" role="img" aria-label="Radiating halftone dot pattern in white on black"></div>
    <div class="temperature-disc">
      <span class="kelvin">6500K</span>
      <span class="label">WHITE BIAS LIGHTING</span>
    </div>
  </div>
</div>
</body>
</html>
```